Every Shelf Set Neatly or ESN Organized needs a business card design. ESN Organized is a professi

We need a business card design that is clean, sharp and conveys a sense of organization. I already have a logo.

Target Market(s)

Families (specifically mothers), small business owners, parents, seniors

Industry/Entity Type

Business

Contact Information for Business Card

My website is www.esnorganized-example.com and my Facebook page is http://www.sociallink-example.com/everyshelfsetneatly. The phone number is 418-552-7094 and I want to be listed as Lorna M. Pelham, Owner

Requirements
Must have
• My logo.

```html
<!DOCTYPE html>
<html lang="en">
<head>
<meta charset="utf-8">
<title>ESN Organized – Business Card</title>
<link rel="stylesheet" href="https://fonts.googleapis.com/css2?family=Open+Sans:ital,wght@0,400;0,600;1,400&display=swap">
<style>
  :root {
    --backdrop: #8d8d8f;
    --card-light: #e8e9eb;
    --card-dark: #000000;
    --brand-blue: #1a73c7;
    --ink: #333438;
    --ink-soft: #1e1f22;
    --paper-white: #ffffff;
  }
  html, body {
    margin: 0;
    padding: 0;
    width: 1105px;
    height: 1200px;
    overflow: hidden;
    background: var(--backdrop);
    font-family: "Open Sans", Arial, sans-serif;
  }
  .canvas {
    position: relative;
    width: 1105px;
    height: 1200px;
  }
  .card {
    position: absolute;
    left: 182px;
    width: 747px;
    height: 427px;
    box-sizing: border-box;
  }
  .card--front { top: 119px; background: var(--card-light); }
  .card--back  { top: 637px; background: var(--card-dark); }

  .owner {
    position: absolute;
    right: 59px;
    top: 50px;
    text-align: right;
  }
  .owner__name {
    margin: 0;
    font-size: 26px;
    font-weight: 600;
    color: var(--brand-blue);
    line-height: 1.2;
  }
  .owner__title {
    margin: 2px 0 0;
    font-size: 19px;
    color: var(--ink-soft);
  }
  .accent-bar {
    position: absolute;
    right: 0;
    top: 55px;
    width: 19px;
    height: 56px;
    background: var(--brand-blue);
  }
  .brand-name {
    position: absolute;
    left: 0;
    right: 0;
    top: 172px;
    margin: 0;
    text-align: center;
    font-size: 34px;
    font-weight: 400;
    line-height: 1.2;
    color: var(--ink-soft);
    white-space: nowrap;
  }
  .contact {
    position: absolute;
    left: 55px;
    top: 296px;
    margin: 0;
    padding: 0;
    list-style: none;
  }
  .contact__item {
    display: flex;
    align-items: center;
    height: 28px;
    font-size: 19px;
    color: var(--ink);
  }
  .contact__icon {
    width: 18px;
    height: 18px;
    margin-right: 8px;
    flex: none;
  }
  .back-name {
    position: absolute;
    left: 0;
    right: 0;
    top: 170px;
    margin: 0;
    text-align: center;
    font-size: 56px;
    font-weight: 400;
    line-height: 1.2;
    color: var(--brand-blue);
  }
  .back-url {
    position: absolute;
    left: 0;
    right: 0;
    top: 352px;
    margin: 0;
    text-align: center;
    font-size: 19px;
    font-style: italic;
    letter-spacing: 5px;
    color: var(--paper-white);
  }
</style>
</head>
<body>
<main class="canvas">
  <section class="card card--front" aria-label="Card front">
    <div class="owner">
      <p class="owner__name">Lorna M. Pelham</p>
      <p class="owner__title">Owner</p>
    </div>
    <div class="accent-bar"></div>
    <p class="brand-name">ESN Organized</p>
    <ul class="contact">
      <li class="contact__item">
        <svg class="contact__icon" viewBox="0 0 24 24" aria-hidden="true">
          <path fill="var(--brand-blue)" d="M6.6 10.8a15.1 15.1 0 0 0 6.6 6.6l2.2-2.2a1 1 0 0 1 1-.25 11.4 11.4 0 0 0 3.6.57 1 1 0 0 1 1 1V20a1 1 0 0 1-1 1A17 17 0 0 1 3 4a1 1 0 0 1 1-1h3.5a1 1 0 0 1 1 1c0 1.25.2 2.45.57 3.57a1 1 0 0 1-.25 1z"/>
        </svg>
        418-552-7094
      </li>
      <li class="contact__item">
        <svg class="contact__icon" viewBox="0 0 24 24" aria-hidden="true">
          <circle cx="12" cy="12" r="10" fill="var(--brand-blue)"/>
          <path d="M2 12h20M12 2c3 3 3 17 0 20M12 2c-3 3-3 17 0 20" stroke="var(--card-light)" stroke-width="1.4" fill="none"/>
        </svg>
        www.esnorganized-example.com
      </li>
      <li class="contact__item">
        <svg class="contact__icon" viewBox="0 0 24 24" aria-hidden="true">
          <g fill="none" stroke="var(--brand-blue)" stroke-width="2.6" stroke-linecap="round">
            <path d="M10 14a4.5 4.5 0 0 0 6.4 0l3.2-3.2a4.5 4.5 0 0 0-6.4-6.4L11.6 6"/>
            <path d="M14 10a4.5 4.5 0 0 0-6.4 0l-3.2 3.2a4.5 4.5 0 0 0 6.4 6.4l1.6-1.6"/>
          </g>
        </svg>
        everyshelfsetneatly
      </li>
    </ul>
  </section>

  <section class="card card--back" aria-label="Card back">
    <p class="back-name">ESN Organized</p>
    <p class="back-url">www.esnorganized-example.com</p>
  </section>
</main>
</body>
</html>
```